Wellness bold & beautiful PowerPoint Template

I will like a PowerPoint template, matching my brand, designed for my business.
- Some words that describe our brand identity are: wellness, natural, calming, simplicity, clean
- For icons, we prefer line icons.
- Website: http://www.vendrabo.com/
- PowerPoint board: https://www.pinterest.com/morelistavy/vendrabo-powerpoint/
- Branding board: https://www.pinterest.com/morelistavy/vendrabo-branding/
FYI: I am attaching a rough draft of a powerpoint presentation we are preparing
Target Market(s)
Women 23-48 interested in wellness
Industry/Entity Type
Health And Wellness
Font styles to use
Other font styles liked:
- Open Sans, Helvitica, Meddon
Requirements
Must have
- cover page, about page, author page, table of content, table format, graph format, list format, 2 column template.
Nice to have
- time line page sample

```html
<!DOCTYPE html>
<html lang="en">
<head>
<meta charset="UTF-8">
<title>About Us – Vendrabo Wellness</title>
<link rel="stylesheet" href="https://fonts.googleapis.com/css2?family=Open+Sans:wght@400;700&display=swap">
<style>
  :root {
    --leaf-dark: #0b2a12;
    --leaf-mid: #1f6b34;
    --leaf-bright: #3ea35a;
    --panel: #dfe7e2;
    --panel-edge: #e9eeea;
    --frame-line: #5b9a3c;
    --accent-magenta: #b3218f;
    --ink: #1d1d1d;
  }
  * { margin: 0; padding: 0; box-sizing: border-box; }
  html, body {
    width: 1200px;
    height: 675px;
    overflow: hidden;
    background: var(--leaf-dark);
  }
  .slide {
    position: relative;
    width: 1200px;
    height: 675px;
    overflow: hidden;
    font-family: "Open Sans", Arial, sans-serif;
  }
  .foliage-backdrop {
    position: absolute;
    inset: 0;
    background:
      radial-gradient(circle at 8% 15%, var(--leaf-bright) 0%, transparent 22%),
      radial-gradient(circle at 92% 12%, var(--leaf-bright) 0%, transparent 20%),
      radial-gradient(circle at 10% 88%, var(--leaf-bright) 0%, transparent 22%),
      radial-gradient(circle at 90% 90%, var(--leaf-bright) 0%, transparent 22%),
      linear-gradient(135deg, var(--leaf-mid), var(--leaf-dark) 50%, var(--leaf-mid));
  }
  .content-panel {
    position: absolute;
    left: 78px;
    top: 45px;
    width: 1050px;
    height: 585px;
    background: radial-gradient(ellipse at center, var(--panel) 0%, var(--panel-edge) 100%);
  }
  .panel-frame {
    position: absolute;
    left: 100px;
    top: 68px;
    width: 1000px;
    height: 539px;
    border: 2px solid var(--frame-line);
  }
  .about-copy {
    position: absolute;
    left: 100px;
    width: 1000px;
    top: 272px;
    text-align: center;
    color: var(--ink);
  }
  .about-title {
    font-weight: 700;
    font-size: 94px;
    line-height: 1.1;
    letter-spacing: 1px;
    color: var(--accent-magenta);
  }
  .about-tagline {
    margin-top: 28px;
    font-size: 30px;
    font-weight: 400;
    line-height: 1.2;
  }
  .about-tagline .quote-mark {
    font-size: 40px;
    vertical-align: 4px;
    margin: 0 6px;
  }
  .about-mission {
    margin-top: 10px;
    font-size: 24px;
    line-height: 44px;
  }
</style>
</head>
<body>
  <main class="slide">
    <div class="foliage-backdrop" role="img" aria-label="Dense green leafy branches covering a dark background, with leaf sprigs reaching into each corner"></div>
    <div class="content-panel" role="img" aria-label="Soft translucent white panel with a faint pale leaf pattern"></div>
    <div class="panel-frame"></div>
    <section class="about-copy">
      <h1 class="about-title">ABOUT US</h1>
      <p class="about-tagline"><span class="quote-mark">“</span>Supporting your wellness journey<span class="quote-mark">”</span></p>
      <p class="about-mission">Helping people live healthier (happier), more<br>balanced and holistic lives</p>
    </section>
  </main>
</body>
</html>
```